Business card design needed

Family General Practitioner/ Family Physician.
Logo is the logo of the Noble Guild of Family Healers Oceania
http://kpltw.varendo.example/ImageShelf/marks/pages/NGFHO%20mark_jpg.htm
Updates

Project Deadline Extended
Reason: Just a bit more time to make changes and the weekend for me to look at things closely and to choose. Thanks, Orin

Thanks for all the submissions. So many of them are really works of art. Not one of them are not good. The ones that I am eliminating are the ones that I think are not suitable for me personally only, and because if I don't, it makes it very difficult to decide as many of you are also sending me slight variations of a card. I have just decided to choose a second place card too. Can't thank you all enough. Good luck, Orin. P.S - Working today till 10 pm as the card says :-), so probably won't be able to give a feedback till late Saturday night or Sunday morning here in Sydney, Australia. 

Project Deadline Extended
Reason: Just added a second place to the budget and realised that Australia is ahead of the rest of the world in the time zone (only :-) - don't want to offend anyone or start a debate!! ) , so Monday deadline will mean it will be a weekend for the rest of the world. Just wanted to give everyone more time to submit their best, especially since I will be picking a second card too. Can't thank everyone enough for the submissions. P.S - Not keen on photos on the card.

Industry/Entity Type

Business

Contact Information for Business Card

Dr. Orin Halvey M.B.B.S., F.N.G.F.H.O
Family General Practitioner
Address, timings, phone and fax number on the back.

Requirements
Must have
• Timings
Mon 7 am - 7 pm
Tues 7 am - 12 pm
Wed 7 am - 10 pm
Thurs 7 am - 12 pm
Fri 7 am - 8 pm
Sat 8 am - 10 pm
Sun - Off

```html
<!DOCTYPE html>
<html lang="en">
<head>
<meta charset="utf-8">
<title>Dr. Orin Halvey – Business Card</title>
<link rel="stylesheet" href="https://fonts.googleapis.com/css2?family=Libre+Bodoni&family=Playfair+Display&family=Oswald:wght@200&display=swap">
<style>
  :root {
    --navy: #110e4e;
    --ink: #0f2a55;
    --paper: #ffffff;
    --periwinkle: #7b7fc4;
    --petal: #aab3dc;
    --ghost: #dcdcdc;
    --hours-text: #ffffff;
  }
  html, body {
    margin: 0;
    padding: 0;
    overflow: hidden;
    background: var(--paper);
  }
  .card {
    position: relative;
    width: 1200px;
    height: 682px;
    overflow: hidden;
    background: var(--paper);
  }
  .hours-panel {
    position: absolute;
    left: 0;
    top: 0;
    width: 282px;
    height: 682px;
    background: var(--navy);
  }
  .hours {
    position: absolute;
    left: 48px;
    top: 12px;
    margin: 0;
    font-family: "Libre Bodoni", serif;
    font-size: 25px;
    line-height: 44px;
    color: var(--hours-text);
    letter-spacing: -0.6px;
  }
  .hours-title { margin: 0; font: inherit; }
  .hours-list { margin: 0; padding: 0; list-style: none; }
  .hours-list li { display: flex; white-space: nowrap; }
  .hours-day { width: 80px; flex: none; }
  .panel-flowers {
    position: absolute;
    left: 60px;
    top: 378px;
    width: 205px;
    height: 304px;
    background: linear-gradient(180deg, rgba(110,120,200,0.5) 0%, rgba(110,120,200,0.15) 25%, rgba(110,120,200,0) 100%);
  }
  .bloom-spray {
    position: absolute;
    left: 78px;
    top: 560px;
    width: 500px;
    height: 122px;
    border-radius: 250px 250px 0 0;
    background: radial-gradient(ellipse at 50% 100%, rgba(120,130,200,0.85) 0%, rgba(170,179,220,0.6) 55%, rgba(170,179,220,0) 100%);
  }
  .doctor-first {
    position: absolute;
    left: 441px;
    top: 236px;
    margin: 0;
    font-family: "Playfair Display", serif;
    font-weight: 400;
    font-size: 36px;
    color: var(--periwinkle);
  }
  .surname {
    position: absolute;
    left: 470px;
    top: 204px;
  }
  .contact {
    position: absolute;
    left: 846px;
    top: 552px;
    margin: 0;
    font-family: "Playfair Display", serif;
    font-size: 39px;
    line-height: 52px;
    color: var(--ink);
    letter-spacing: -1px;
  }
  .contact p { margin: 0; }
</style>
</head>
<body>
<div class="card">
  <aside class="hours-panel">
    <div class="hours">
      <h2 class="hours-title">Office Hours</h2>
      <ul class="hours-list">
        <li><span class="hours-day">Mon.</span>7 am - 7 pm</li>
        <li><span class="hours-day">Tues.</span>7 am - 12 pm</li>
        <li><span class="hours-day">Wed.</span>7 am - 10 pm</li>
        <li><span class="hours-day">Thurs.</span>7 am - 12 pm</li>
        <li><span class="hours-day">Fri.</span>7 am - 8 pm</li>
        <li><span class="hours-day">Sat.</span>8 am - 10 pm</li>
        <li><span class="hours-day">Sun.</span>Closed</li>
      </ul>
    </div>
    <div class="panel-flowers" role="img" aria-label="Three small blue daisies on tall thin stems"></div>
  </aside>

  <div class="bloom-spray" role="img" aria-label="Large soft blue flower petals rising from the bottom edge"></div>

  <svg class="surname" width="560" height="420" viewBox="0 0 560 420" role="img" aria-label="Halvey">
    <defs>
      <linearGradient id="reflection-fade" x1="0" y1="0" x2="0" y2="1">
        <stop offset="0" stop-color="#fff" stop-opacity="0.55"/>
        <stop offset="1" stop-color="#fff" stop-opacity="0"/>
      </linearGradient>
      <mask id="reflection-mask">
        <rect x="0" y="202" width="560" height="200" fill="url(#reflection-fade)"/>
      </mask>
    </defs>
    <g class="reflection-lines" stroke-width="1" opacity="0.5">
      <line x1="22" y1="202" x2="22" y2="400" stroke="#e8d8a8"/>
      <line x1="105" y1="202" x2="105" y2="400" stroke="#f0c8b8"/>
      <line x1="160" y1="202" x2="160" y2="400" stroke="#e8e0b0"/>
      <line x1="230" y1="202" x2="230" y2="400" stroke="#f0c8b8"/>
      <line x1="290" y1="202" x2="290" y2="400" stroke="#e8d8a8"/>
      <line x1="355" y1="202" x2="355" y2="400" stroke="#f0c8b8"/>
      <line x1="420" y1="202" x2="420" y2="400" stroke="#e8e0b0"/>
      <line x1="490" y1="202" x2="490" y2="400" stroke="#f0c8b8"/>
    </g>
    <text x="10" y="202" textLength="530" lengthAdjust="spacing"
          font-family="Oswald, sans-serif" font-weight="200" font-size="232" fill="#dcdcdc">HALVEY</text>
    <g mask="url(#reflection-mask)">
      <text x="10" y="202" textLength="530" lengthAdjust="spacing" transform="translate(0 404) scale(1 -1)"
            font-family="Oswald, sans-serif" font-weight="200" font-size="232" fill="#dcdcdc">HALVEY</text>
    </g>
  </svg>

  <h1 class="doctor-first">DR. ORIN</h1>

  <div class="contact">
    <p>P: 02 5550 1400</p>
    <p>F:&nbsp; 02 5550 1233</p>
  </div>
</div>
</body>
</html>
```